Naturopath Practitioner Card Design

I am a naturopath needing a design for a business card mainly to show that I am a naturopath and have some contact details to give to prospective clients. I am open minded about the design and what is on the second side of the card whether it just be some artwork or space for details, appointment times etc. Naturopathy is the practice of natural medicine that uses a holistic approach and incorporates herbal and nutritional medicine.

Industry/Entity Type

Business

Contact Information for Business Card

Tom Rudd NaturopathBHSc (Naturopathy) Member WHPG 0487 925 316 tom.rudd@mailexample.com www.tomruddnaturopathy.example.au

Requirements
Nice to have
• Would prefer some kind of original pattern/art work/logo rather than an image, not fussed if its very simple/basic
• I am open to any colour but think I would prefer a more earthy sandy clay etc type style than the greens that are commonly associated with naturopathy.
Should not have
• Don't really want to have generic stock images on it

```html
<!DOCTYPE html>
<html lang="en">
<head>
<meta charset="utf-8">
<title>Tom Rudd Naturopath – Business Card</title>
<link href="https://fonts.googleapis.com/css2?family=Arimo:wght@400;700&family=Tinos:wght@400;700&display=swap" rel="stylesheet">
<style>
  :root {
    --page: #e9e6e1;
    --card-white: #f7f7f7;
    --ink-red: #a3141b;
    --band-red: #9a0c12;
    --ink-dark: #2a2a2a;
    --dots: #555;
    --black: #050505;
    --white: #ffffff;
    --soft-grey: #c9c9c9;
  }
  * { box-sizing: border-box; margin: 0; padding: 0; }
  html, body { width: 1200px; height: 902px; overflow: hidden; }
  body {
    background: var(--page);
    display: flex; flex-direction: column; align-items: center; justify-content: center;
    gap: 56px;
    font-family: "Arimo", Arial, sans-serif;
  }
  .card {
    position: relative; width: 640px; height: 366px; overflow: hidden;
    box-shadow: 0 6px 18px rgba(0,0,0,.18);
  }

  /* Appointment side */
  .card--appointment { background: var(--card-white); }
  .appointment__title {
    position: absolute; top: 34px; left: 0; right: 0; text-align: center;
    font-family: "Tinos", "Times New Roman", serif; font-weight: 700;
    font-size: 46px; color: var(--ink-red); letter-spacing: .5px;
  }
  .field {
    position: absolute; left: 44px; right: 44px; display: flex; align-items: flex-end; gap: 10px;
    font-size: 20px; color: var(--ink-red);
  }
  .field__line { flex: 1; border-bottom: 2px dotted var(--dots); height: 1px; margin-bottom: 5px; }
  .field--for { top: 118px; }
  .field--date { top: 164px; }
  .field--blank { top: 258px; }
  .days {
    position: absolute; top: 216px; left: 44px; right: 44px;
    display: flex; justify-content: space-between;
    font-size: 17px; color: var(--ink-dark);
  }
  .day { display: flex; align-items: center; gap: 6px; }
  .day__box { width: 17px; height: 17px; border: 2px solid var(--ink-dark); }
  .appointment__rule { position: absolute; left: 0; right: 0; bottom: 48px; height: 3px; background: var(--soft-grey); }
  .appointment__band { position: absolute; left: 0; right: 0; bottom: 0; height: 40px; background: var(--band-red); }

  /* Contact side */
  .card--contact { background: radial-gradient(ellipse at 70% 80%, #1d2024 0%, var(--black) 60%); color: var(--white); }
  .contact__photo {
    position: absolute; left: 150px; top: 150px; width: 450px; height: 140px;
    background: radial-gradient(ellipse at 55% 50%, #4a5a3c 0%, #2a3326 40%, rgba(10,12,12,0) 75%);
    opacity: .8;
  }
  .contact__identity { position: absolute; left: 40px; top: 150px; }
  .contact__name {
    font-family: "Tinos", "Times New Roman", serif; font-weight: 700;
    font-size: 48px; line-height: 1; margin-bottom: 8px;
  }
  .contact__role { font-size: 20px; line-height: 1.3; color: #ececec; white-space: nowrap; }
  .contact__divider { position: absolute; left: 372px; top: 40px; width: 2px; height: 120px; background: var(--white); }
  .contact__details { position: absolute; left: 388px; top: 62px; font-size: 16px; line-height: 1.9; }
  .contact__item { display: flex; align-items: center; gap: 8px; white-space: nowrap; }
  .contact__item svg { width: 15px; height: 15px; flex: none; }
  .contact__rule { position: absolute; left: 0; right: 0; bottom: 56px; height: 3px; background: #e0e0e0; }
  .contact__band { position: absolute; left: 0; right: 0; bottom: 0; height: 50px; background: var(--band-red); }
</style>
</head>
<body>

  <section class="card card--appointment" aria-label="Appointment side">
    <h2 class="appointment__title">Appointment</h2>
    <div class="field field--for"><span>For:</span><span class="field__line"></span></div>
    <div class="field field--date"><span>Date:</span><span class="field__line"></span><span>Time:</span><span class="field__line"></span></div>
    <div class="days">
      <span class="day"><span class="day__box"></span>MON.</span>
      <span class="day"><span class="day__box"></span>TUE.</span>
      <span class="day"><span class="day__box"></span>WED.</span>
      <span class="day"><span class="day__box"></span>THU.</span>
      <span class="day"><span class="day__box"></span>FRI.</span>
      <span class="day"><span class="day__box"></span>SAT.</span>
    </div>
    <div class="field field--blank"><span class="field__line"></span></div>
    <div class="appointment__rule"></div>
    <div class="appointment__band"></div>
  </section>

  <section class="card card--contact" aria-label="Contact side">
    <div class="contact__photo" role="img" aria-label="Soft dark photo area of a relaxing herbal treatment setting with leaves"></div>
    <div class="contact__identity">
      <h1 class="contact__name">Tom Rudd</h1>
      <p class="contact__role">Naturopath<br>BHSc (Naturopathy) Member WHPG</p>
    </div>
    <div class="contact__divider"></div>
    <div class="contact__details">
      <p class="contact__item">
        <svg viewBox="0 0 16 16" aria-hidden="true"><rect x="1" y="1" width="14" height="14" fill="#fff"/><path d="M5 4c1 0 1.5 2 1 2.5L5.5 7c.5 1.2 1.5 2.2 2.7 2.7l.5-.5c.5-.5 2.5 0 2.5 1 0 .8-1 1.8-2 1.8C6 12 4 10 4 6.2 4 5 4.5 4 5 4z" fill="#000"/></svg>
        0487 925 316
      </p>
      <p class="contact__item">
        <svg viewBox="0 0 16 16" aria-hidden="true"><rect x="1" y="1" width="14" height="14" fill="#fff"/><rect x="3.5" y="5" width="9" height="6" fill="none" stroke="#000" stroke-width="1.2"/><path d="M3.5 5L8 8.5 12.5 5" fill="none" stroke="#000" stroke-width="1.2"/></svg>
        tom.rudd@mailexample.com
      </p>
    </div>
    <div class="contact__rule"></div>
    <div class="contact__band"></div>
  </section>

</body>
</html>
```